Doorhanger

Create a 3.5" x 8.5" door hanger for a produce delivery company called Mama Kettle's.

Door hanger should fit the template specifications attached.

Door hanger should include some form of the logo attached.

Door hanger should include the information: "Fresh, local produce, meats, dairy, cheese, and baked goods. Delivered to your door at grocery store prices!"

Door hanger should include the following coupon: "$15.00 OFF! Enter coupon code “doorhanger” during sign up and we’ll waive the enrollment fee and take $5.00 of your first order!"

Door hanger should have the website printed noticeably: MamaKettles.example

Door hanger should include photos of seasonal produce items to the southern US. Some examples include: apples, pumpkins, bell peppers, squashes, eggplant, tomatoes, green beans, carrots, broccoli, greens, sweet potatoes, lettuces, cauliflower, cabbage, radishes.

Industry/Entity Type

Grocery Store

Requirements
Nice to have
• A back side with some or all of the following "About us" information:
• Mama Kettle's is a farm to fork delivery service, working to bring the entire NC food landscape to your front door! Since 2008 we have been expanding our network of local growers and food artisans, and are happy to be able to offer over 200 food products a week, and we are still growing! Our goal is to greatly improve access to local foods in our community through transparency, communication, affordability, and the convenience of our delivery infrastructure.
• Here are just a few reasons we think you will love working with Mama Kettle's:
• Wide variety of NC products!
• You will not find a greater variety of NC produce anywhere else, outside of a farmers market.
• Superior freshness, quality, and flavor!
• By working with local growers, products can be fully ripened on the vine, picked and delivered to your door within 48 hours of harvest.
• Affordable!
• We understand that affordability is an important concern for every family. On average our prices are equivalent to grocery store prices when comparing like items (organic to organic, etc.).
• Support your community!
• By purchasing from local farms and food artisans, you are supporting your neighbors and helping to further develop our local food infrastructure.
• Educational!
• Purchasing seasonal products from local farms is a fantastic opportunity to get back to nature and reconnect with what food really is.
• Convenient and easy!
• Not to mention, we deliver to your front door! Easy!

```html
<!DOCTYPE html>
<html lang="en">
<head>
<meta charset="utf-8">
<title>Mama Kettle's Door Hangers</title>
<link href="https://fonts.googleapis.com/css2?family=Roboto+Condensed:wght@400;700&family=Open+Sans:wght@600;700&display=swap" rel="stylesheet">
<style>
  :root {
    --page: #ecebe8;
    --red: #d8141a;
    --red-dark: #a30d10;
    --green: #3c9a2c;
    --green-dark: #23731e;
    --band-green: #3f8f3a;
    --white: #ffffff;
    --ink: #1d1d1d;
    --rust: #a2261a;
    --wood-light: #d9b68c;
    --wood-mid: #c49a6c;
    --wood-dark: #a97c50;
  }
  * { box-sizing: border-box; margin: 0; padding: 0; }
  html, body { width: 1200px; height: 900px; overflow: hidden; background: var(--page); }
  body { position: relative; font-family: "Roboto Condensed", "Arial Narrow", sans-serif; }

  .hanger {
    position: absolute;
    width: 310px;
    height: 820px;
    overflow: hidden;
    box-shadow: 0 4px 14px rgba(0,0,0,.25);
  }
  .hanger--green { left: 153px; top: 40px; background: var(--white); }
  .hanger--wood { left: 783px; top: 40px; background: linear-gradient(90deg, var(--wood-mid), var(--wood-light) 30%, var(--wood-mid) 55%, var(--wood-light) 80%, var(--wood-dark)); }

  .hanger__hole {
    position: absolute; left: 135px; top: 42px; width: 100px; height: 100px;
    border-radius: 50%; background: var(--page); z-index: 5;
  }
  .hanger__slit {
    position: absolute; left: 180px; top: 0; width: 2px; height: 48px;
    background: var(--page); z-index: 5;
  }

  .photo { position: absolute; }
  .photo--eggplant { left: 0; top: 0; width: 310px; height: 300px;
    background: linear-gradient(160deg, #e4e2e5 0%, #cfc8cf 40%, #6b3f66 75%, #3a2a3b 100%); }
  .photo--peas { left: 0; top: 515px; width: 310px; height: 250px;
    background: linear-gradient(170deg, #6a6356 0%, #7d8a4b 45%, #6fa53a 70%, #4b4a42 100%); }
  .photo--basket { left: 2px; top: 250px; width: 300px; height: 262px; border-radius: 50%;
    background: radial-gradient(ellipse at 45% 55%, #c0303a 0%, #8d2a3c 40%, #5a3146 65%, #b08a5a 85%, #8e6638 100%); }

  .green-band {
    position: absolute; left: 0; top: 297px; width: 310px; height: 218px;
    background: linear-gradient(180deg, #2f7a2c, var(--band-green) 40%, #2d6f2b);
  }

  .coupon {
    position: absolute; width: 242px; padding: 8px 10px 10px;
    color: var(--white); text-align: center; z-index: 6;
    box-shadow: 0 3px 8px rgba(0,0,0,.35);
    border: 1px solid rgba(255,255,255,.6);
  }
  .coupon--red { left: 32px; top: 160px; background: linear-gradient(180deg, var(--red), var(--red-dark)); transform: rotate(-2deg); }
  .coupon--green { left: 30px; top: 152px; background: linear-gradient(180deg, var(--green), var(--green-dark)); transform: rotate(2deg); }
  .coupon__title { font-weight: 700; font-size: 29px; line-height: 1.05; letter-spacing: .5px; }
  .coupon__body { font-size: 17px; line-height: 1.3; margin-top: 4px; }

  .pitch { position: absolute; font-weight: 700; z-index: 3; }
  .pitch--light { left: 0; top: 337px; width: 310px; text-align: center; color: var(--white); font-size: 20px; line-height: 30px; }
  .pitch--light .pitch__lead { font-size: 25px; }
  .pitch--rust { right: 12px; top: 520px; width: 290px; text-align: right; color: var(--rust); font-size: 20px; line-height: 29.5px; }
  .pitch--rust .pitch__lead { font-size: 27px; line-height: 36px; }

  .swoosh { position: absolute; left: 0; width: 310px; }
  .swoosh--green { top: 650px; height: 120px; }
  .swoosh--wood { top: 650px; height: 170px; }

  .brand {
    position: absolute; display: flex; flex-direction: column; align-items: center; gap: 6px; z-index: 4;
  }
  .brand--left { left: 18px; top: 660px; }
  .brand--right { left: 8px; top: 680px; }
  .brand__mark { width: 70px; height: 70px; border-radius: 50%; border: 2px solid var(--ink); }
  .brand__name { font-weight: 700; font-size: 19px; color: var(--ink); letter-spacing: 1px; }

  .footer-band {
    position: absolute; left: 0; top: 770px; width: 310px; height: 50px;
    background: linear-gradient(180deg, var(--band-green), var(--green-dark));
  }
  .footer-band__tab {
    position: absolute; left: 32px; top: 8px; width: 250px; height: 34px;
    background: var(--white); border-radius: 14px 14px 4px 4px;
    font-family: "Open Sans", Arial, sans-serif; font-weight: 600; font-size: 17px;
    color: var(--green-dark); text-align: center; line-height: 34px;
  }
  .url-small {
    position: absolute; left: 20px; top: 786px; font-family: "Open Sans", Arial, sans-serif;
    font-weight: 700; font-size: 11px; color: var(--ink); letter-spacing: .3px; z-index: 4;
  }
</style>
</head>
<body>

<section class="hanger hanger--green" aria-label="Door hanger, green version">
  <div class="photo photo--eggplant" role="img" aria-label="Photo of small purple eggplants and a bell pepper"></div>
  <div class="hanger__hole"></div><div class="hanger__slit"></div>

  <div class="coupon coupon--red">
    <p class="coupon__title">15.00 $ OFF!</p>
    <p class="coupon__body">Enter coupon code<br>“doorhanger”<br>during sign up and we’ll waive<br>the enrollment fee and take<br>$5.00 of your first order!</p>
  </div>

  <div class="green-band"></div>
  <p class="pitch pitch--light"><span class="pitch__lead">Fresh... Local produce...</span><br>Meats, Dairy, Cheese<br>&amp; Baked goods.<br>Delivered to your door<br>at grocery store prices!</p>

  <div class="photo photo--peas" role="img" aria-label="Photo of green pea pods and loose peas on wood"></div>

  <svg class="swoosh swoosh--green" viewBox="0 0 310 120" preserveAspectRatio="none" aria-hidden="true">
    <path d="M0 40 C90 0 200 20 310 80 L310 120 L0 120 Z" fill="#ffffff"/>
  </svg>
  <div class="brand brand--left">
    <div class="brand__mark"></div>
    <span class="brand__name">MAMA KETTLE'S</span>
  </div>

  <div class="footer-band"><div class="footer-band__tab">www.MamaKettles.example</div></div>
</section>

<section class="hanger hanger--wood" aria-label="Door hanger, wood version">
  <div class="hanger__hole"></div><div class="hanger__slit"></div>

  <div class="photo photo--basket" role="img" aria-label="Photo of a woven basket with red onions, peppers, tomatoes and eggplant"></div>

  <div class="coupon coupon--green">
    <p class="coupon__title">15.00 $ OFF!</p>
    <p class="coupon__body">Enter coupon code<br>“doorhanger”<br>during sign up and we’ll waive<br>the enrollment fee and take<br>$5.00 of your first order!</p>
  </div>

  <p class="pitch pitch--rust"><span class="pitch__lead">Fresh... Local produce...</span><br>Meats, Dairy, Cheese &amp;<br>Baked goods.<br>Delivered to your door<br>at grocery store<br>prices!</p>

  <svg class="swoosh swoosh--wood" viewBox="0 0 310 170" preserveAspectRatio="none" aria-hidden="true">
    <path d="M0 20 C60 0 130 40 200 110 C240 145 280 158 310 160 L310 170 L0 170 Z" fill="#ffffff"/>
  </svg>
  <div class="brand brand--right">
    <div class="brand__mark"></div>
    <span class="brand__name">MAMA KETTLE'S</span>
  </div>
  <p class="url-small">MAMAKETTLES.EXAMPLE</p>
</section>

</body>
</html>
```